Wordpress Design Project

Hi,

I would like a more modern colourful design doing for my website ZAP Lnx (www.za%plnx.com - remove percentage). But I do still want to keep the same sort of colors, just maybe lighter. More interesting.

I want the inside pages to NOT all look the same with just boring text.

I want the site to look more appealing and maybe a new logo.
Updates

I would like to mention I would prefer to keep the same logo after rethinking it (possibly a slight refresh of the logo if you feel its a good idea) and the same color scheme as at present.

Saves us rebranding a lot of our apps, tools online ads etc.

Also I thought it is worth mentioning we have 2 parts to the site. The front end and the logged in area. It would be good if when making the front end you keep in mind the back end at http://p.za%plnx.com (remove percentage). We can only edit this limitedly (can edit the entire footer, the logo and full CSS of it). Would be good if we could make sure the header and footer can be used on the back end as well maybe to make it match.

I also want layouts making not just for the homepage. Obviously every page will basically be the same but I don't want all the other pages to just be 'text' and no real layout.

You can see out main pages on the website at the moment, I want those other pages to be laid out nice and differently as well. For example the testimonials page could be more interesting with speech bubbles and pictures of each person (just use placeholders). The affiliates page could be a description and then a nice fancy list of features why to join etc. 

Nothing overly complicated but I think it makes the whole site seem a lot better.

Target Market(s)

Affiliate Marketing. International.

Requirements
Must have
• Needs to be more room for links across the navigation at the top, also sub menus (at present we have a lot of pages which are hidden deep within other pages).
Nice to have
• Lists of features for advertisers and affiliates on the homepage part.

Menu items and buttons have nice hover over effects.

I want to get across on our pages all the different unique features we have.

Maybe some kind of slider which has past offer logos in, just use example logos.

```html
<!DOCTYPE html>
<html lang="en">
<head>
<meta charset="utf-8">
<title>ZAP Lnx – International Affiliate Network</title>
<link rel="stylesheet" href="https://fonts.googleapis.com/css2?family=Oswald:wght@500;600&family=Ropa+Sans&family=Signika:wght@400;600&family=Roboto:wght@400;500&display=swap">
<style>
:root{
  --orange:#f7941d;
  --orange-dark:#e07f0c;
  --teal:#6bb5ae;
  --teal-dark:#1e5550;
  --teal-text:#4fa7a0;
  --teal-line:#3f8f89;
  --pale:#eaf3f2;
  --stripe:#dbe8e6;
  --grey-text:#7a7a7a;
  --dark:#222;
  --yellow:#fdd33a;
  --yellow-dark:#f3b413;
  --white:#fff;
}
*{box-sizing:border-box;margin:0;padding:0}
html,body{width:893px;height:1200px;overflow:hidden;background:var(--white)}
body{position:relative;font-family:"Roboto",Arial,sans-serif;color:var(--grey-text)}
.abs{position:absolute}

/* header */
.brand{left:126px;top:8px;font:600 44px/1 "Signika",sans-serif;color:var(--orange);letter-spacing:-1px}
.brand-dot{position:absolute;left:197px;top:6px;width:14px;height:14px;border-radius:50%;background:var(--teal)}
.login-btn{left:718px;top:12px;width:50px;height:22px;border-radius:4px;background:linear-gradient(#8fd3cc,#5fb5ad);color:#fff;font:13px/22px "Roboto",sans-serif;text-align:center;box-shadow:0 1px 2px rgba(0,0,0,.2)}
.phone{left:622px;top:46px;font:600 19px/1 "Signika",sans-serif;color:#111}

/* nav */
.main-nav{left:0;top:77px;width:893px;height:26px;background:var(--orange);border-bottom:1px solid var(--orange-dark)}
.main-nav ul{list-style:none;position:absolute;left:131px;top:0;display:flex;height:26px}
.main-nav li{font:15px/26px "Ropa Sans",sans-serif;color:#fff;padding:0 5px;margin-right:15px;text-transform:uppercase;letter-spacing:.3px}
.main-nav li.active{background:var(--teal)}

/* hero */
.hero{left:0;top:103px;width:893px;height:393px;background:var(--teal);overflow:hidden}
.hero-rule{height:1px;background:var(--teal-line)}
.hero-kicker{left:0;width:893px;top:18px;text-align:center;font:600 19px/1 "Oswald",sans-serif;color:var(--teal-dark);letter-spacing:1px}
.hero-title{left:0;width:893px;top:44px;text-align:center;font:600 32px/1 "Oswald",sans-serif;color:#fff;letter-spacing:.5px}
.hero-shot{left:265px;top:102px;width:320px;height:142px;border-radius:3px;background:linear-gradient(160deg,#f4f7f8,#d8e2e3);box-shadow:0 8px 18px rgba(0,0,0,.25)}
.hero-team{left:268px;top:290px;width:332px;height:103px;background:linear-gradient(#cfcfcf,#8d8d8d);border-radius:60px 60px 0 0}

/* intro columns */
.intro{left:0;top:496px;width:893px;height:152px;background:var(--pale)}
.intro-col{top:12px;width:322px}
.intro-col h2{font:600 20px/1 "Signika",sans-serif;color:var(--orange);letter-spacing:.5px;margin-bottom:10px}
.intro-col p{font-size:11.3px;line-height:16px;color:#555}
.cta{display:block;width:128px;height:32px;margin-top:12px;border-radius:4px;background:linear-gradient(var(--yellow),var(--yellow-dark));box-shadow:0 2px 0 #c98f08;font:600 16px/32px "Signika",sans-serif;color:#222;text-align:center}
.band{left:0;top:648px;width:893px;height:9px;background:var(--stripe)}

/* login */
.account{left:112px;top:673px;width:158px;height:184px;background:#f1f1f1;border-radius:4px}
.account h3{position:absolute;left:15px;top:12px;font:15px/1 "Ropa Sans",sans-serif;color:var(--dark);letter-spacing:.3px}
.field{position:absolute;left:14px;width:130px;height:28px;background:#fff;border-radius:4px;font:11.5px/28px "Roboto",sans-serif;color:#333;padding-left:8px}
.forgot{position:absolute;left:15px;top:124px;font-size:9.5px;color:#333}
.login-row{position:absolute;left:14px;top:146px;font-size:9.5px;color:#333;display:flex;align-items:center;gap:6px}
.login-row span.btn{width:48px;height:22px;border:1px solid #aaa;border-radius:4px;background:linear-gradient(#fafafa,#ddd);font:500 11px/20px "Roboto",sans-serif;text-align:center;color:#222}

/* welcome */
.welcome{left:299px;top:673px;width:484px}
.welcome h1{font:400 22px/1 "Signika",sans-serif;color:var(--teal-text);margin-bottom:12px;letter-spacing:.3px}
.welcome p{font-size:10.4px;line-height:14px;margin-bottom:8px}

/* sidebar */
.side-head{font:400 15px/1 "Signika",sans-serif;color:var(--teal-text);text-transform:uppercase}
.blog-list{left:112px;top:903px;width:158px;list-style:none}
.blog-list li{font-size:10.3px;height:21px;line-height:21px;border-bottom:1px solid #eee;color:#666;padding-left:9px;position:relative}
.blog-list li:before{content:"›";position:absolute;left:0}
.blog-rule{left:112px;top:972px;width:158px;height:2px;background:#ddd}
.social{left:113px;top:1017px;display:flex;gap:11px}
.social span{width:30px;height:30px;border-radius:4px}

/* why join */
.why{left:299px;top:884px;width:227px;height:166px;background:var(--orange);border-radius:5px;padding:11px 14px}
.why h3{font:400 15px/1 "Signika",sans-serif;color:#fff;margin-bottom:10px}
.why li{list-style:none;font-size:10.2px;line-height:13px;color:#fff;margin-bottom:4.5px;padding-left:6px;position:relative}
.why li:before{content:"›";position:absolute;left:0}

/* testimonial */
.testi{left:556px;top:893px;width:226px}
.testi blockquote{font-size:10.3px;line-height:16px;color:#555;margin-top:9px}
.testi-rule{left:556px;top:1040px;width:226px;height:1px;background:#ccc}
.testi-notch{left:735px;top:1040px}
.testi-name{left:600px;top:1050px;width:175px;text-align:right;font-size:10.3px;color:#333}

/* app badges */
.badges{left:221px;top:1093px;display:flex;gap:16px}
.badge{width:100px;height:28px;border:1px solid #cfe0de;background:#f7fafa;display:flex;align-items:center;padding-left:6px;gap:5px}
.badge i{width:16px;height:16px;border-radius:50%;background:var(--teal)}
.badge b{display:block;font:600 7px/1 "Roboto",sans-serif;color:var(--teal-line)}
.badge small{display:block;font-size:5px;color:#777;margin-top:1px}

/* footer */
.footer{left:0;top:1135px;width:893px;height:65px;background:var(--pale)}
.footer-stripe{left:0;top:0;width:893px;height:10px;background:var(--stripe)}
.footer-links{left:0;top:21px;width:893px;display:flex;justify-content:center;font-size:9.8px;color:#333;gap:0}
.footer-links span{padding:0 20px}
.footer-links em{font-style:normal;color:#555}
.copyright{left:0;top:42px;width:893px;text-align:center;font-size:9.8px;color:#777}
</style>
</head>
<body>

<header>
  <div class="abs brand">ZAP Lnx<span class="brand-dot"></span></div>
  <div class="abs login-btn">Login</div>
  <div class="abs phone">+44 (0)1555 014273</div>
</header>

<nav class="abs main-nav">
  <ul>
    <li class="active">Home</li><li>About Us</li><li>Our Blog</li><li>Testimonials</li><li>Affiliates</li><li>Advertisers</li><li>Contact Us</li>
  </ul>
</nav>

<section class="abs hero">
  <div class="abs hero-rule" style="left:112px;top:28px;width:670px"></div>
  <div class="abs hero-kicker"><span style="background:var(--teal);padding:0 8px">INTERNATIONAL</span></div>
  <div class="abs hero-title">AFFILIATE NETWORK</div>
  <div class="abs hero-shot" role="img" aria-label="Screenshots of the affiliate dashboard and settings panel"></div>
  <div class="abs hero-rule" style="left:112px;top:272px;width:250px"></div>
  <div class="abs hero-rule" style="left:527px;top:272px;width:255px"></div>
  <svg class="abs" style="left:380px;top:252px" width="134" height="40" viewBox="0 0 134 40" aria-label="Join us today">
    <polygon points="0,2 114,2 134,20 114,38 0,38 8,20" fill="#fdc52a"/>
    <text x="63" y="26" text-anchor="middle" font-family="Oswald, sans-serif" font-weight="600" font-size="15" fill="#1a1a1a">JOIN US TODAY!</text>
  </svg>
  <div class="abs hero-team" role="img" aria-label="Group photo of smiling network team members"></div>
</section>

<section class="abs intro">
  <div class="abs intro-col" style="left:112px">
    <h2>AFFILIATES</h2>
    <p>Get access to a wide range of top performing offers for your websites and email marketing lists. Fresh and exclusive offers to promote. Join over 2,000 affiliates already signed up to ZAP Lnx.</p>
    <span class="cta">SIGN UP NOW</span>
  </div>
  <div class="abs intro-col" style="left:460px">
    <h2>ADVERTISERS</h2>
    <p>Generate sales/leads to your website instantly with the ZAP Lnx Affiliate Network. Only pay on performance, no monthly or setup fees. ZAP Lnx takes the risk out of advertising.</p>
    <span class="cta">SIGN UP NOW</span>
  </div>
</section>
<div class="abs band"></div>

<aside class="abs account">
  <h3>ACCOUNT LOGIN</h3>
  <div class="field" style="top:41px">Email</div>
  <div class="field" style="top:84px">Password</div>
  <div class="forgot">Forgot Password</div>
  <div class="login-row"><span class="btn">LOGIN</span>or Sign Up</div>
</aside>

<main class="abs welcome">
  <h1>WELCOME TO ZAP LNX</h1>
  <p>Welcome to the ZAP Lnx affiliate network. On time payments, hot &amp; exclusive CPL/CPA offers, fast support and low fees for advertisers, is the making of a leading affiliate network!</p>
  <p>ZAP Lnx offer a wide range of advertisers for your websites. So you can start monetizing your traffic or get an additional revenue stream, today.</p>
  <p>With the ZAP Lnx Affiliate Network we focus on lead generation offers. We have a range of competitions, surveys, incentives and gambling offers. Whatever the industry, you will be able to find offers to suit your traffic.</p>
  <p>ZAP Lnx is a powerful performance-based internet marketing network dedicated to advertisers to affiliates through its powerful affiliate network.</p>
</main>

<div class="abs side-head" style="left:112px;top:881px">Recent Blog Posts</div>
<ul class="abs blog-list">
  <li>New Offers For China</li><li>NEW: Banner Rotators</li><li style="border:0">New Offers</li>
</ul>
<div class="abs blog-rule"></div>
<div class="abs side-head" style="left:112px;top:992px">Social Networking</div>
<div class="abs social">
  <span style="background:#3b5998"></span><span style="background:#5fc6ea"></span><span style="background:#c4302b"></span><span style="background:#1f6fa3"></span>
</div>

<section class="abs why">
  <h3>WHY JOIN ZAP LNX?</h3>
  <ul>
    <li>High Payouts</li><li>Reliable Tracking</li><li>Great Affiliate Support</li><li>Exclusive Offers</li>
    <li>Monthly/Bi-monthly/Weekly Payments<br>(more info)</li><li>View Stats on Your Mobile</li>
  </ul>
</section>

<section class="abs testi">
  <div class="side-head">Testimonials</div>
  <blockquote>"I decided to start using ZAP Lnx after using several other ZAP sites. I was impressed with the customer service and support provided in comparison to some other networks I have used. ZAP Lnx also has a large range of offers, retailers so is the perfect solution to earning commission. Payments are always on-time too."</blockquote>
</section>
<div class="abs testi-rule"></div>
<svg class="abs testi-notch" width="14" height="8" viewBox="0 0 14 8"><polygon points="0,0 14,0 4,8" fill="#fff" stroke="#ccc"/><line x1="0" y1="0" x2="14" y2="0" stroke="#fff" stroke-width="2"/></svg>
<div class="abs testi-name">Marla Penwick – Siteloom</div>

<div class="abs badges">
  <div class="badge"><i></i><div><b>Mobile Stats</b><small>ZAP Lnx Mobile Website</small></div></div>
  <div class="badge"><i></i><div><b>Blaze Browser</b><small>Official ZAP Lnx Extension</small></div></div>
  <div class="badge"><i></i><div><b>Orbit Browser</b><small>Official ZAP Lnx Extension</small></div></div>
  <div class="badge"><i></i><div><b>Pocket App</b><small>Official ZAP Lnx App</small></div></div>
</div>

<footer class="abs footer">
  <div class="abs footer-stripe"></div>
  <div class="abs footer-links">
    <span>Affiliate Terms &amp; Conditions</span><em>|</em><span>Advertiser Terms &amp; Conditions</span><em>|</em><span>Privacy Policy &amp; Cookies</span><em>|</em><span>FAQ</span><em>|</em><span>Contact Us</span>
  </div>
  <div class="abs copyright">© 2013 ZAP Media UK Ltd - All Rights Reserved.</div>
</footer>

</body>
</html>
```